Animal Eye Clinic needs a Business card

We are a new veterinary ophthalmology practice (Ridgeline Pet Vision Care) and we need a business card designed. We only see animal eyes - we are not a regular veterinary clinic. We already have a logo. We are looking for a professional, good looking business card to hand out to our clients. We are looking for something simple but professional and contemporary. Our logo is likely the only picture/graphic that needs to be on the card.
Updates

Contact Information for Business Card

Delia Vossman, BSc, DVM, MSc, DipACVO
Veterinary Ophthalmologist

Phone: 250.418.3927
Email: ridgelinepetvisioncare@mailbox-example.net
Website: ridgelinepetvisioncare-example.net
Address: 1874 Thornbury Rd
Kelowna, BC, V1X 4M9

Colors

Designer to choose colors to be used in the design.

Requirements
Must have
• Our logo (attached)

```html
<!DOCTYPE html>
<html lang="en">
<head>
<meta charset="utf-8">
<title>Ridgeline Pet Vision Care – Business Card</title>
<link href="https://fonts.googleapis.com/css2?family=Oswald:wght@500&family=Roboto:wght@300;400;500&display=swap" rel="stylesheet">
<style>
  :root {
    --backdrop: #3b3b3c;
    --card: #2b2b2c;
    --teal: #1a9aae;
    --white: #f2f2f2;
    --muted: #d8d8d8;
    --divider: #8a8a8a;
    --faint: rgba(255,255,255,0.04);
  }
  * { margin: 0; padding: 0; box-sizing: border-box; }
  html, body {
    width: 1200px; height: 901px; overflow: hidden;
    background: var(--backdrop);
    font-family: "Roboto", Arial, sans-serif;
  }
  .canvas {
    width: 1200px; height: 901px;
    display: flex; flex-direction: column; align-items: center; justify-content: center;
    gap: 40px;
  }
  .card {
    position: relative; overflow: hidden;
    width: 660px; height: 377px;
    background: var(--card);
    box-shadow: 0 10px 30px rgba(0,0,0,0.35);
  }
  .card__halo {
    position: absolute; border-radius: 50%;
    background: var(--faint);
  }
  .card--front .card__halo { width: 300px; height: 300px; right: -40px; top: 60px; }
  .card--back .card__halo { width: 300px; height: 300px; left: 170px; top: 40px; }

  .brand { display: flex; align-items: center; gap: 14px; position: relative; }
  .brand__dot { width: 46px; height: 46px; border-radius: 50%; background: var(--teal); flex: none; }
  .brand__name { color: var(--teal); font-family: "Roboto", Arial, sans-serif; font-weight: 500; line-height: 1.1; }
  .brand__top { display: block; font-size: 15px; letter-spacing: 0.55em; }
  .brand__bottom { display: block; font-size: 27px; letter-spacing: 0.01em; }

  .card--front .brand { position: absolute; left: 150px; top: 148px; }

  .card--back .brand { position: absolute; left: 40px; top: 128px; }
  .card--back .brand__dot { width: 38px; height: 38px; }
  .card--back .brand__top { font-size: 12px; }
  .card--back .brand__bottom { font-size: 21px; }

  .divider {
    position: absolute; left: 326px; top: 110px;
    width: 1px; height: 120px; background: var(--divider);
  }
  .contact { position: absolute; left: 346px; top: 108px; color: var(--white); }
  .contact__name {
    font-family: "Oswald", Arial, sans-serif; font-weight: 500;
    color: var(--teal); font-size: 17px; letter-spacing: 0.02em; text-transform: uppercase;
  }
  .contact__role { font-size: 14px; font-weight: 300; margin-top: 2px; color: var(--muted); }
  .contact__list { list-style: none; margin-top: 14px; }
  .contact__item { display: flex; align-items: center; gap: 8px; font-size: 12.5px; font-weight: 300; line-height: 1.7; }
  .contact__item svg { width: 12px; height: 12px; fill: var(--teal); flex: none; }
  .contact__accent { color: var(--teal); }

  .address {
    position: absolute; left: 0; right: 0; bottom: 34px;
    text-align: center; color: var(--white); font-size: 15px; font-weight: 300;
  }
  .band { position: absolute; left: 0; right: 0; bottom: 0; height: 10px; background: var(--teal); }
</style>
</head>
<body>
<main class="canvas">
  <section class="card card--front">
    <div class="card__halo"></div>
    <div class="brand">
      <span class="brand__dot"></span>
      <span class="brand__name">
        <span class="brand__top">RIDGELINE</span>
        <span class="brand__bottom">PET VISION CARE</span>
      </span>
    </div>
  </section>

  <section class="card card--back">
    <div class="card__halo"></div>
    <div class="brand">
      <span class="brand__dot"></span>
      <span class="brand__name">
        <span class="brand__top">RIDGELINE</span>
        <span class="brand__bottom">PET VISION CARE</span>
      </span>
    </div>
    <div class="divider"></div>
    <div class="contact">
      <p class="contact__name">Delia Vossman, BSc, DVM, MSc, DipACVO</p>
      <p class="contact__role">Veterinary Ophthalmologist</p>
      <ul class="contact__list">
        <li class="contact__item">
          <svg viewBox="0 0 24 24" aria-hidden="true"><path d="M6.6 10.8a15.1 15.1 0 0 0 6.6 6.6l2.2-2.2a1 1 0 0 1 1-.25 11.4 11.4 0 0 0 3.6.57 1 1 0 0 1 1 1V20a1 1 0 0 1-1 1A17 17 0 0 1 3 4a1 1 0 0 1 1-1h3.5a1 1 0 0 1 1 1c0 1.25.2 2.45.57 3.57a1 1 0 0 1-.25 1z"/></svg>
          250.418.3927
        </li>
        <li class="contact__item">
          <svg viewBox="0 0 24 24" aria-hidden="true"><path d="M2 5h20v14H2z M3.5 6.5l8.5 6 8.5-6" fill="var(--teal)"/></svg>
          ridgelinepetvisioncare@mailbox-example.net
        </li>
        <li class="contact__item">
          <svg viewBox="0 0 24 24" aria-hidden="true"><circle cx="12" cy="12" r="10"/></svg>
          <span>www.<span class="contact__accent">ridgelinepetvisioncare-example</span>.net</span>
        </li>
      </ul>
    </div>
    <p class="address">1874 Thornbury Rd, Kelowna, BC, V1X 4M9</p>
    <div class="band"></div>
  </section>
</main>
</body>
</html>
```